Veldmark Supplies Business Card

Professional business card that stand out to our potential customers. Front and back with clean modern design

Industry/Entity Type

Oil and gas

Contact Information for Business Card

Name, address, website , office phone and cell number

Requirements
Must have
• Editable files for each employee

```html
<!DOCTYPE html>
<html lang="en">
<head>
<meta charset="utf-8">
<title>Veldmark Supplies Business Card</title>
<link href="https://fonts.googleapis.com/css2?family=Roboto:wght@400;500;700&display=swap" rel="stylesheet">
<style>
  :root {
    --stage: #2b2b2b;
    --card-black: #1c1c1e;
    --card-panel: #262628;
    --brand-red: #e01b22;
    --brand-blue: #27a9d8;
    --emboss: #3a3a3d;
    --emboss-edge: #4a4a4e;
    --text-light: #e9e9e9;
    --white: #ffffff;
  }
  * { margin: 0; padding: 0; box-sizing: border-box; }
  html, body { width: 1200px; height: 852px; overflow: hidden; }
  body {
    background: var(--stage);
    font-family: "Roboto", Arial, sans-serif;
    position: relative;
  }
  .card {
    position: absolute;
    width: 500px;
    height: 286px;
    border-radius: 22px;
    overflow: hidden;
  }
  .card--back {
    left: 80px; top: 150px;
    background: var(--card-black);
    display: flex; flex-direction: column; align-items: center; justify-content: center; gap: 14px;
  }
  .back-mark {
    width: 58px; height: 58px;
    border: 3px solid var(--emboss-edge);
    background: var(--emboss);
  }
  .back-name {
    color: var(--emboss-edge);
    font-weight: 700;
    font-size: 26px;
    letter-spacing: 3px;
    text-transform: uppercase;
  }
  .card--front {
    left: 620px; top: 412px;
    background: var(--card-panel);
  }
  .front-shape { position: absolute; inset: 0; }
  .front-brand {
    position: absolute; left: 26px; top: 108px; width: 210px;
    display: flex; flex-direction: column; align-items: center; gap: 12px;
  }
  .front-brand__mark { width: 44px; height: 44px; background: var(--white); }
  .front-brand__name {
    color: var(--white); font-weight: 700; font-size: 22px; letter-spacing: 1px;
    text-transform: uppercase; text-align: center; line-height: 1.2;
  }
  .contact {
    position: absolute; left: 300px; top: 42px;
    color: var(--text-light); font-size: 12px; line-height: 1.45;
  }
  .contact__name { color: var(--brand-blue); font-size: 20px; font-weight: 500; }
  .contact__title { font-size: 12px; margin-bottom: 22px; }
  .contact__address { margin-bottom: 8px; }
  .contact__row { display: flex; align-items: center; gap: 7px; }
  .contact__icon { width: 10px; height: 10px; flex: none; }
</style>
</head>
<body>
  <div class="card card--back">
    <div class="back-mark"></div>
    <div class="back-name">Veldmark Supplies</div>
  </div>

  <div class="card card--front">
    <svg class="front-shape" viewBox="0 0 500 286" width="500" height="286">
      <path d="M0,0 L178,0 Q282,70 288,286 L0,286 Z" fill="var(--brand-blue)"/>
      <path d="M0,0 L160,0 Q266,70 272,286 L0,286 Z" fill="var(--brand-red)"/>
    </svg>
    <div class="front-brand">
      <div class="front-brand__mark"></div>
      <div class="front-brand__name">Veldmark<br>Supplies</div>
    </div>
    <div class="contact">
      <div class="contact__name">Jordan Hale</div>
      <div class="contact__title">Managing Director</div>
      <div class="contact__address">418 W. Larkspur Ave Suite 3<br>Brinwell, Tx 79702</div>
      <div class="contact__row">
        <svg class="contact__icon" viewBox="0 0 10 10"><path d="M1,3 Q5,0 9,3 L8,5 L6,4 L4,4 L2,5 Z M2,6 L8,6 L8,9 L2,9 Z" fill="var(--brand-red)"/></svg>
        <span>(555)214-0387</span>
      </div>
      <div class="contact__row">
        <svg class="contact__icon" viewBox="0 0 10 10"><rect x="0.5" y="2" width="9" height="6.5" fill="var(--brand-red)"/><path d="M0.5,2 L5,5.5 L9.5,2" stroke="var(--card-panel)" fill="none"/></svg>
        <span>sales@veldmarksupplies.com</span>
      </div>
      <div class="contact__row">
        <svg class="contact__icon" viewBox="0 0 10 10"><circle cx="5" cy="5" r="4.5" fill="var(--brand-red)"/><path d="M0.5,5 H9.5 M5,0.5 V9.5" stroke="var(--card-panel)" stroke-width="0.8"/></svg>
        <span>www.veldmarksupplies.com</span>
      </div>
    </div>
  </div>
</body>
</html>
```